Tessmar Fahrwerkstatt
Sehr angenehme zusammenarbeit nicht aufdringlich und genau auf die Wünsche eingegangen. Wir werde sicher noch mehr zusammen Arbeiten. Gruss Lukas Hegemann Inhaber Tessmar Fahrwerkstatt
Zielgruppe
Dinks und Kunden mit viel Erfolg und hohem Ausgabepotential.
Aufgabenstellung
Unsere Firma vertreibt Fahrzeuge im Luxusbereich hauptgebiet Valmerra aber auch andere Sportwagen. Was uns fehlt ist ein optischer Wiedererkennugswert. Deshalb hätten wir gerne ein Visitenkarten Design und Briefpapier Design. Später soll auch noch eine Webseite mit gleichem Wiedererkennungswert entstehen. " Roter Faden "

```html
<!DOCTYPE html>
<html lang="de">
<head>
<meta charset="utf-8">
<title>Tessmar Fahrwerkstatt – Briefpapier</title>
<link rel="stylesheet" href="https://fonts.googleapis.com/css2?family=Merriweather:wght@400;700&display=swap">
<style>
  :root {
    --band: #5a7590;
    --sheet-back: #587690;
    --paper: #ffffff;
    --address-field: #e8e9e8;
    --ink: #2b2b2b;
    --brand: #4d6a86;
    --canvas: #ffffff;
  }
  * { margin: 0; padding: 0; box-sizing: border-box; }
  html, body { width: 1200px; height: 845px; overflow: hidden; background: var(--canvas); }
  body { position: relative; font-family: "Merriweather", Georgia, serif; color: var(--ink); }

  .top-band { position: absolute; left: 0; top: 0; width: 1200px; height: 12px; background: var(--band); }

  .sheet-back {
    position: absolute; left: 576px; top: 140px; width: 491px; height: 641px;
    background: var(--sheet-back);
    box-shadow: 0 2px 8px rgba(0,0,0,.25);
  }
  .back-mark {
    position: absolute; left: 379px; top: 526px; width: 74px; height: 79px;
    background: var(--paper); border-radius: 10px;
  }

  .letter {
    position: absolute; left: 195px; top: 100px; width: 485px; height: 637px;
    background: var(--paper);
    box-shadow: 0 2px 10px rgba(0,0,0,.3);
  }

  .brand { position: absolute; left: 38px; top: 31px; display: flex; align-items: center; gap: 7px; }
  .brand-square { width: 24px; height: 24px; background: var(--brand); border-radius: 3px; }
  .brand-name { font-size: 12px; line-height: 13px; font-weight: 400; color: var(--brand); letter-spacing: .8px; text-transform: lowercase; }

  .address-field {
    position: absolute; left: 38px; top: 113px; width: 170px; height: 88px;
    background: var(--address-field);
  }
  .address { position: absolute; left: 17px; top: 44px; font-size: 6px; line-height: 8px; font-weight: 700; font-style: normal; }

  .letter-body {
    position: absolute; left: 45px; top: 251px; width: 265px;
    font-size: 6px; line-height: 10px; font-weight: 700;
  }
  .letter-body p { margin-bottom: 5px; }
  .letter-body .salutation { margin-bottom: 8px; }
  .letter-body .closing { margin-top: 8px; margin-bottom: 18px; }

  .contact-column {
    position: absolute; left: 349px; top: 556px; width: 115px;
    font-size: 4.6px; line-height: 6px; font-weight: 700; font-style: normal;
  }
  .contact-column .label { font-weight: 400; }
  .contact-column .group { margin-bottom: 2px; }
</style>
</head>
<body>
  <div class="top-band"></div>

  <div class="sheet-back">
    <div class="back-mark"></div>
  </div>

  <div class="letter">
    <div class="brand">
      <div class="brand-square"></div>
      <div class="brand-name">tessmar<br>fahrwerkstatt</div>
    </div>

    <div class="address-field">
      <address class="address">max mustermann<br>musterstrasse 7<br>ch 3917 seewinkel</address>
    </div>

    <div class="letter-body">
      <p class="salutation">sehr geehrte damen und herren,</p>
      <p>wir danken ihnen für ihr interesse an unseren fahrzeugen und freuen uns, ihnen heute unser aktuelles angebot vorstellen zu dürfen. jedes fahrzeug wird in unserer werkstatt sorgfältig geprüft, gepflegt und für die übergabe vorbereitet. unsere berater nehmen sich zeit für ihre wünsche und begleiten sie von der ersten probefahrt bis zur auslieferung. gerne zeigen wir ihnen auch ausgewählte sportwagen weiterer marken, die wir mit derselben sorgfalt betreuen. auf wunsch organisieren wir finanzierung, versicherung und zulassung, damit sie sich ganz auf das fahren konzentrieren können. ob klassischer gran turismo oder moderner sportwagen, wir legen grossen wert auf transparenz bei historie, wartung und ausstattung. sämtliche unterlagen stellen wir ihnen vollständig zur verfügung, damit sie ihre entscheidung in ruhe treffen können.</p>
      <p>gerne laden wir sie zu einer persönlichen beratung in unseren ausstellungsraum ein. dort stehen ihnen unsere fachleute für alle fragen rund um ausstattung, leistung und wartung zur verfügung. vereinbaren sie einfach einen termin, der ihnen passt, und erleben sie ihr wunschfahrzeug aus nächster nähe. selbstverständlich bereiten wir das gewünschte fahrzeug vor ihrem besuch vor, sodass sie es ausgiebig besichtigen und auf einer probefahrt kennenlernen können. auch ein abholservice ist möglich.</p>
      <p>wir freuen uns darauf, von ihnen zu hören, und stehen ihnen jederzeit telefonisch oder per e-mail zur verfügung. gerne senden wir ihnen auch weitere unterlagen zu unseren modellen, serviceleistungen und aktuellen angeboten zu. ein kurzer anruf genügt, und wir melden uns umgehend.</p>
      <p class="closing">mit freundlichen grüssen</p>
      <p>max mustermann</p>
    </div>

    <address class="contact-column">
      <div class="group"><span class="label">telefon</span><br>+41 52 617 48 09<br>info@tessmar.ch<br>www.tessmar.ch</div>
      <div class="group"><span class="label">adresse</span><br>werkhofstrasse 4, 3917 seewinkel</div>
      <div class="group"><span class="label">postfach</span><br>postfach 12, 3917 seewinkel</div>
    </address>
  </div>
</body>
</html>
```